Clinic for cellulit and fat removal

Name of clinic :
Lirava
- Body & Health (this has to be written on the site.)
I need CMS for me to be able to make changes myself.
A webpage for woman searching for a solution to remove fat and cellulit.
The owner is a brazilian woman in Denmark, and want her sense of aestetic shines thru the website.
There needs to be a slide show on the landing page showing big sliding pictures, of the clinic and and the treatments.
The Cryolipolysis, is a treatment freezing fat and cellulit, and this treatment will be the Attraction of the clinic.
Needs These pages in a horisontal fasion. (written in Danish)
Lirava
Behandlinger
- Cryolipolysis
- Trimflox
- Lymfemassage
- Korathelix
- Amberline Tide
Produkter
Priser
Kontakt
Clinic
Coded - Design and coding required
5+ page

```html
<!DOCTYPE html>
<html lang="en">
<head>
<meta charset="utf-8">
<title>Lirava – Body &amp; Health</title>
<link href="https://fonts.googleapis.com/css2?family=Jost:wght@400;500;600&display=swap" rel="stylesheet">
<style>
:root{
  --teal:#2cbbb8;
  --teal-dark:#22a8a5;
  --ink:#1d1d1d;
  --text:#6a6a6a;
  --muted:#9a9a9a;
  --line:#e2e2e2;
  --white:#ffffff;
  --skin-a:#c9a999;
  --skin-b:#8f7466;
}
*{box-sizing:border-box;margin:0;padding:0}
html,body{width:1200px;height:3358px;overflow:hidden}
body{font-family:"Jost",sans-serif;color:var(--text);background:var(--white);position:relative}
.abs{position:absolute}
.btn-outline{position:absolute;border:1.5px solid var(--teal);color:var(--teal);border-radius:22px;font-size:11px;font-weight:500;letter-spacing:.5px;display:flex;align-items:center;justify-content:center;width:130px;height:36px}
.heading{position:absolute;left:0;width:1200px;text-align:center;color:var(--ink);font-size:29px;font-weight:500;letter-spacing:.5px}
.copy{font-size:13.5px;line-height:24px;color:var(--text)}

/* header / hero */
.hero{position:absolute;left:0;top:0;width:1200px;height:537px;background:linear-gradient(120deg,#5e4a41 0%,#a88a79 35%,#cdb3a3 55%,#9a7f71 80%,#4b3a33 100%)}
.hero::after{content:"";position:absolute;inset:0;background:rgba(0,0,0,.22)}
.nav{position:absolute;top:36px;left:0;width:1200px;height:36px;z-index:2}
.brand{position:absolute;left:98px;top:0;color:var(--white);font-size:33px;font-weight:500;letter-spacing:1px;line-height:36px}
.nav-link{position:absolute;top:0;line-height:36px;color:var(--white);font-size:13px;font-weight:500;letter-spacing:.5px}
.nav-link.active{color:var(--teal)}
.nav-phone{position:absolute;left:840px;top:0;width:172px;height:40px;border:1.5px solid var(--white);border-radius:20px;color:var(--white);font-size:14px;display:flex;align-items:center;justify-content:center;gap:8px}
.hero-sub{position:absolute;top:186px;width:1200px;text-align:center;color:var(--white);font-size:24px;z-index:2}
.hero-title{position:absolute;top:228px;width:1200px;text-align:center;color:var(--white);font-size:76px;font-weight:500;letter-spacing:1px;z-index:2}
.hero-btn{position:absolute;left:479px;top:338px;width:242px;height:45px;border:1.5px solid var(--white);border-radius:23px;color:var(--white);font-size:14px;font-weight:500;display:flex;align-items:center;justify-content:center;z-index:2}
.dots{position:absolute;top:470px;left:0;width:1200px;display:flex;justify-content:center;gap:6px;z-index:2}
.dots span{width:14px;height:14px;border:2px solid var(--white);border-radius:50%}
.dots span.on{background:var(--white)}

.photo{position:absolute;border:6px solid #fff;box-shadow:0 0 0 1px var(--line)}
.arrow-btn{position:absolute;width:40px;height:40px;border:1.5px solid #cfcfcf;border-radius:50%;display:flex;align-items:center;justify-content:center}

.card-title{position:absolute;top:1330px;font-size:20px;font-weight:500;color:var(--ink)}
.card-text{position:absolute;top:1375px;width:305px}

.products{position:absolute;left:0;top:1583px;width:1200px;height:405px;background:linear-gradient(100deg,#dfe2e6 0%,#b9c3cf 22%,#4f7fa6 34%,#b8a196 52%,#8d776c 70%,#c7b2a6 100%)}
.products::after{content:"";position:absolute;inset:0;background:rgba(60,45,40,.25)}
.products .inner{position:absolute;left:605px;top:56px;width:495px;z-index:2;color:var(--white)}

.blog-title{position:absolute;font-size:15px;font-weight:600;color:var(--ink)}
.meta{position:absolute;font-size:11px;color:var(--text);display:flex;align-items:center;gap:6px}

.feedback{position:absolute;left:0;top:2409px;width:1200px;height:354px;background:var(--teal)}
.quote{position:absolute;top:128px;width:236px;color:var(--white);font-size:12.5px;line-height:19px}
.quote-mark{position:absolute;top:118px;color:var(--white);font-size:36px;font-style:italic;line-height:36px}
.avatar{position:absolute;top:128px;width:72px;height:72px;border-radius:50%;border:3px solid #fff;background:linear-gradient(160deg,#d8c3b4,#8e7a6e)}
.person{position:absolute;top:256px;color:var(--white);font-size:10px;font-weight:600}
.role{position:absolute;top:271px;color:var(--white);font-size:9.5px;font-style:italic}

.label{position:absolute;font-size:11px;color:var(--text);letter-spacing:.5px}
.field{position:absolute;border:1px solid #cfcfcf}
.sub-head{position:absolute;font-size:14px;font-weight:500;color:var(--ink);letter-spacing:.3px}
.info-icon{position:absolute;left:808px;width:40px;height:40px;border:1.5px solid #d4d4d4;border-radius:50%;display:flex;align-items:center;justify-content:center}
.info-text{position:absolute;left:889px;font-size:13px;color:var(--text)}
.hours{position:absolute;font-size:13px;color:var(--text)}
.social{position:absolute;top:3306px;width:26px;height:26px;background:#b5b5b5;border-radius:3px}
</style>
</head>
<body>

<header class="hero" role="img" aria-label="Slideshow photo of a body contouring treatment on a client's leg">
</header>
<nav class="nav">
  <div class="brand">LIRAVA</div>
  <span class="nav-link active" style="left:316px">LIRAVA</span>
  <span class="nav-link" style="left:405px">BEHANDLINGER</span>
  <span class="nav-link" style="left:549px">PRODUKTER</span>
  <span class="nav-link" style="left:669px">PRISER</span>
  <span class="nav-link" style="left:746px">KONTAKT</span>
  <span class="nav-phone"><svg width="14" height="14" viewBox="0 0 24 24"><path fill="#fff" d="M6.6 10.8a15 15 0 0 0 6.6 6.6l2.2-2.2c.3-.3.7-.4 1-.2 1.1.4 2.3.6 3.6.6.6 0 1 .4 1 1V20c0 .6-.4 1-1 1A17 17 0 0 1 3 4c0-.6.4-1 1-1h3.5c.6 0 1 .4 1 1 0 1.3.2 2.5.6 3.6.1.3 0 .7-.2 1z"/></svg>1 555 010 2040</span>
  <span class="nav-link" style="left:1032px;font-size:12px">ENG | DAN</span>
</nav>
<div class="hero-sub">Cellulit and Fat Removal Clinic</div>
<h1 class="hero-title">BODY &amp; HEALTH</h1>
<div class="hero-btn">MAKE AN APPOINTMENT</div>
<div class="dots"><span class="on"></span><span></span><span></span><span></span></div>

<!-- welcome -->
<section>
  <h2 class="abs" style="left:98px;top:598px;font-size:29px;font-weight:500;color:var(--ink)">WELCOME TO LIRAVA</h2>
  <p class="abs copy" style="left:98px;top:660px;width:500px">At vero eos et accusamus et iusto odio dignissimos ducimus qui blanditiis praesen tium voluptatum deleniti atque corrupti quos.</p>
  <p class="abs copy" style="left:98px;top:740px;width:500px">Dolores et quas molestias excepturi sint occaecati cupiditate non provid similiquei sunt in culpa qui officia deserunt mollitia animi, id est laborum et dolorum fu haru m quidem rerum facilis est et expedita disti am libero tem.</p>
  <div class="btn-outline" style="left:98px;top:853px">READ MORE &gt;&gt;</div>
  <div class="photo" role="img" aria-label="Video still of a therapist using a cryolipolysis applicator" style="left:640px;top:605px;width:460px;height:286px;background:linear-gradient(135deg,#e9ecef,#c9d3dc 45%,#d8c5ba 70%,#f1ece8)">
    <svg class="abs" style="left:202px;top:113px" width="56" height="56" viewBox="0 0 56 56"><circle cx="28" cy="28" r="28" fill="#1a1a1a"/><path d="M22 17l18 11-18 11z" fill="#fff"/></svg>
  </div>
  <div class="abs" style="left:98px;top:952px;width:1002px;height:1px;background:var(--line)"></div>
</section>

<!-- treatments -->
<section>
  <h2 class="heading" style="top:1004px">OUR TREATMENTS</h2>
  <div class="arrow-btn" style="left:34px;top:1169px"><svg width="12" height="12" viewBox="0 0 12 12"><path d="M8 1L3 6l5 5" stroke="#999" stroke-width="1.6" fill="none"/></svg></div>
  <div class="arrow-btn" style="left:1124px;top:1169px"><svg width="12" height="12" viewBox="0 0 12 12"><path d="M4 1l5 5-5 5" stroke="#999" stroke-width="1.6" fill="none"/></svg></div>

  <div class="photo" role="img" aria-label="Client lying on a treatment bed during cryolipolysis" style="left:98px;top:1090px;width:310px;height:202px;background:linear-gradient(135deg,#9b8a94,#d9cfd0 45%,#efe9e6)"></div>
  <div class="photo" role="img" aria-label="Waist and hips with contour lines drawn on the skin" style="left:443px;top:1090px;width:312px;height:202px;background:linear-gradient(135deg,#dfe9f2,#e8c9b8 50%,#dfe6ee)"></div>
  <div class="photo" role="img" aria-label="Therapist giving a lymphatic massage on a leg" style="left:790px;top:1090px;width:310px;height:202px;background:linear-gradient(135deg,#eee6df,#d8b39b 55%,#efe6df)"></div>

  <h3 class="card-title" style="left:98px">CRYOLIPOLYSIS</h3>
  <h3 class="card-title" style="left:445px">TRIMFLOX</h3>
  <h3 class="card-title" style="left:790px">LYMFEMASSAGE</h3>
  <p class="card-text copy" style="left:98px">Nam libero tempore, cum soluta nobis est eligen di optio cumque nihil impedit quo minus id quod ma xi me placeat facere possimus</p>
  <p class="card-text copy" style="left:445px">Nam libero tempore, cum soluta nobis est eligen di optio cumque nihil impedit quo minus id quod ma xi me placeat facere possimus</p>
  <p class="card-text copy" style="left:790px">Nam libero tempore, cum soluta nobis est eligen di optio cumque nihil impedit quo minus id quod ma xi me placeat facere possimus</p>
  <div class="btn-outline" style="left:98px;top:1475px">READ MORE &gt;&gt;</div>
  <div class="btn-outline" style="left:445px;top:1475px">READ MORE &gt;&gt;</div>
  <div class="btn-outline" style="left:790px;top:1475px">READ MORE &gt;&gt;</div>
</section>

<!-- products -->
<section class="products" role="img" aria-label="Gloved hands applying a blue treatment device to a client's thigh">
  <div class="inner">
    <h2 style="font-size:29px;font-weight:500;letter-spacing:.5px">OUR PRODUCTS</h2>
    <p class="copy" style="color:#fff;margin-top:18px">At vero eos et accusamus et iusto odio dignissimos ducimus qui blanditiis praesen tium voluptatum deleniti atque corrupti quos.</p>
    <p class="copy" style="color:#fff;margin-top:24px">Dolores et quas molestias excepturi sint occaecati cupiditate non provid similiquei sunt in culpa qui officia deserunt mollitia animi, id est laborum et dolorum fu haru m quidem rerum facilis est et expedita disti am libero tem.</p>
    <div class="btn-outline" style="position:relative;margin-top:26px;border-color:#fff;color:#fff">READ MORE &gt;&gt;</div>
  </div>
</section>

<!-- blog -->
<section>
  <h2 class="heading" style="top:2061px">LATEST BLOG</h2>
  <div class="photo" role="img" aria-label="Treatment device being applied to a client's stomach" style="left:98px;top:2156px;width:204px;height:179px;background:linear-gradient(135deg,#c7d1d8,#d9c0b1 55%,#b59c8c)"></div>
  <h3 class="blog-title" style="left:329px;top:2150px">FINIBUS BONORUM ET MALORU</h3>
  <div class="meta" style="left:329px;top:2180px"><svg width="11" height="11" viewBox="0 0 12 12"><rect x="1" y="2" width="10" height="9" fill="none" stroke="var(--teal)" stroke-width="1.4"/><path d="M1 5h10" stroke="var(--teal)" stroke-width="1.4"/></svg>08/03/2016 &nbsp;|&nbsp; <svg width="10" height="11" viewBox="0 0 10 11"><circle cx="5" cy="3" r="2.5" fill="var(--teal)"/><path d="M0 11a5 5 0 0 1 10 0z" fill="var(--teal)"/></svg>Mara Lund</div>
  <p class="abs copy" style="left:329px;top:2208px;width:250px">Nam libero tempore, cum soluta nobises tei lig endi optio cumque nihil impedit qu minus id quod maxime plac.</p>
  <div class="btn-outline" style="left:329px;top:2302px">READ MORE &gt;&gt;</div>

  <div class="photo" role="img" aria-label="Therapist treating a client's back with a handheld device" style="left:625px;top:2156px;width:204px;height:179px;background:linear-gradient(135deg,#e3dcd6,#c59a82 55%,#7e6a60)"></div>
  <h3 class="blog-title" style="left:857px;top:2150px">FINIBUS BONORUM ET MALORU</h3>
  <div class="meta" style="left:857px;top:2180px"><svg width="11" height="11" viewBox="0 0 12 12"><rect x="1" y="2" width="10" height="9" fill="none" stroke="var(--teal)" stroke-width="1.4"/><path d="M1 5h10" stroke="var(--teal)" stroke-width="1.4"/></svg>08/03/2016 &nbsp;|&nbsp; <svg width="10" height="11" viewBox="0 0 10 11"><circle cx="5" cy="3" r="2.5" fill="var(--teal)"/><path d="M0 11a5 5 0 0 1 10 0z" fill="var(--teal)"/></svg>Mara Lund</div>
  <p class="abs copy" style="left:857px;top:2208px;width:250px">Nam libero tempore, cum soluta nobises tei lig endi optio cumque nihil impedit qu minus id quod maxime plac.</p>
  <div class="btn-outline" style="left:857px;top:2302px">READ MORE &gt;&gt;</div>
</section>

<!-- feedback -->
<section class="feedback">
  <h2 class="abs" style="left:0;top:46px;width:1200px;text-align:center;color:#fff;font-size:29px;font-weight:500">CUSTOMER FEEDBACK</h2>
  <div class="arrow-btn" style="left:27px;top:152px;width:34px;height:34px;border-color:rgba(255,255,255,.7)"><svg width="10" height="10" viewBox="0 0 12 12"><path d="M8 1L3 6l5 5" stroke="#fff" stroke-width="1.6" fill="none"/></svg></div>
  <div class="arrow-btn" style="left:1139px;top:152px;width:34px;height:34px;border-color:rgba(255,255,255,.7)"><svg width="10" height="10" viewBox="0 0 12 12"><path d="M4 1l5 5-5 5" stroke="#fff" stroke-width="1.6" fill="none"/></svg></div>

  <div class="avatar" role="img" aria-label="Customer portrait" style="left:98px"></div>
  <span class="quote-mark" style="left:188px">"</span>
  <p class="quote" style="left:210px">At vero eos et accusamus et iust odio dignissimos ducimus qui blanditi praesent ium voluptatum deleniti atque cruppus dolores et quas.</p>
  <div class="person" style="left:190px">HELENA ROCHA</div>
  <div class="role" style="left:190px">Financial Wellness Advisor</div>

  <div class="avatar" role="img" aria-label="Customer portrait" style="left:440px"></div>
  <span class="quote-mark" style="left:530px">"</span>
  <p class="quote" style="left:552px">At vero eos et accusamus et iust odio dignissimos ducimus qui blanditi praesent ium voluptatum deleniti atque cruppus dolores et quas.</p>
  <div class="person" style="left:532px">TOBIAS RAVNHOLT</div>
  <div class="role" style="left:532px">Urban Health Fellow</div>

  <div class="avatar" role="img" aria-label="Customer portrait" style="left:792px"></div>
  <span class="quote-mark" style="left:882px">"</span>
  <p class="quote" style="left:904px">At vero eos et accusamus et iust odio dignissimos ducimus qui blanditi praesent ium voluptatum deleniti atque cruppus dolores et quas.</p>
  <div class="person" style="left:884px">SOFIE BRANDT</div>
  <div class="role" style="left:884px">Creative Strategist | Entrepreneur</div>
</section>

<!-- contact -->
<section>
  <h2 class="heading" style="top:2836px">CONTACT US</h2>
  <h3 class="sub-head" style="left:98px;top:2912px">CONTACT FORM</h3>
  <span class="label" style="left:98px;top:2955px">NAME :</span>
  <span class="label" style="left:418px;top:2955px">PHONE NO :</span>
  <div class="field" style="left:98px;top:2980px;width:310px;height:36px"></div>
  <div class="field" style="left:418px;top:2980px;width:312px;height:36px"></div>
  <span class="label" style="left:98px;top:3026px">EMAIL :</span>
  <div class="field" style="left:98px;top:3047px;width:632px;height:36px"></div>
  <span class="label" style="left:98px;top:3092px">MESSAGE :</span>
  <div class="field" style="left:98px;top:3114px;width:632px;height:81px"></div>
  <div class="abs" style="left:634px;top:3206px;width:96px;height:36px;border-radius:18px;background:var(--teal);color:#fff;font-size:13px;font-weight:500;display:flex;align-items:center;justify-content:center">SUBMIT</div>

  <h3 class="sub-head" style="left:808px;top:2912px">CONTACT INFORMATION</h3>
  <div class="info-icon" style="top:2956px"><svg width="14" height="16" viewBox="0 0 14 18"><path d="M7 1a6 6 0 0 0-6 6c0 4.5 6 10 6 10s6-5.5 6-10a6 6 0 0 0-6-6z" fill="none" stroke="var(--teal)" stroke-width="1.6"/><circle cx="7" cy="7" r="2" fill="var(--teal)"/></svg></div>
  <span class="info-text" style="top:2966px">Finibus Bonorum et Malorum</span>
  <div class="info-icon" style="top:3012px"><svg width="14" height="14" viewBox="0 0 24 24"><path fill="var(--teal)" d="M6.6 10.8a15 15 0 0 0 6.6 6.6l2.2-2.2c.3-.3.7-.4 1-.2 1.1.4 2.3.6 3.6.6.6 0 1 .4 1 1V20c0 .6-.4 1-1 1A17 17 0 0 1 3 4c0-.6.4-1 1-1h3.5c.6 0 1 .4 1 1 0 1.3.2 2.5.6 3.6.1.3 0 .7-.2 1z"/></svg></div>
  <span class="info-text" style="top:3022px">1 555 010 2040</span>
  <div class="info-icon" style="top:3070px"><svg width="16" height="12" viewBox="0 0 16 12"><rect x="1" y="1" width="14" height="10" fill="none" stroke="var(--teal)" stroke-width="1.5"/><path d="M1 1l7 6 7-6" fill="none" stroke="var(--teal)" stroke-width="1.5"/></svg></div>
  <span class="info-text" style="top:3080px">info@lirava.com</span>

  <h3 class="sub-head" style="left:808px;top:3136px">WORKING HOURS</h3>
  <span class="hours" style="left:808px;top:3174px">Monday - Friday &nbsp;:</span><span class="hours" style="left:948px;top:3174px">8:30 AM to 5:00 PM</span>
  <span class="hours" style="left:808px;top:3208px">Saturday &nbsp;:</span><span class="hours" style="left:948px;top:3208px">9:00 AM to 2:00 PM</span>
  <span class="hours" style="left:808px;top:3241px">Sunday</span><span class="hours" style="left:948px;top:3241px">Closed</span>
</section>

<footer>
  <div class="abs" style="left:98px;top:3280px;width:1002px;height:1px;background:var(--line)"></div>
  <span class="abs" style="left:98px;top:3310px;font-size:11.5px;color:var(--text)">Copyright © 2017, Lirava. All Rights Reserved.</span>
  <span class="social" style="left:952px"></span>
  <span class="social" style="left:992px"></span>
  <span class="social" style="left:1032px"></span>
  <span class="social" style="left:1072px"></span>
</footer>

</body>
</html>
```